Website for a high end London wedding DJ company

I want a website that is fairly basic but modern. It needs to look professional and smooth. I like white and black backgrounds. I am looking for something similar to this: https://www.torvalinsky.uk - at the bottom of this page it has ravenquill reviews as well. I mainly use bimmlo reviews. This would need to be included, or at least some way of showing all my 5 star reviews on the first page, to get peoples attention.
My current website is www.marrowandtide.com
My

1 page

• A way to display my reviews. Must be modern.
• Must not look cheesy and 8

```html
<!DOCTYPE html>
<html lang="en">
<head>
<meta charset="utf-8">
<title>Marrow &amp; Tide — DJ Hire Surrey</title>
<link rel="stylesheet" href="https://fonts.googleapis.com/css2?family=Playfair+Display:wght@400;700&family=Montserrat:wght@400;500;600&display=swap">
<style>
:root{
  --ink:#0b0b0b;
  --dark:#141414;
  --band:#232323;
  --paper:#ffffff;
  --paper-soft:#f3f3f3;
  --muted:#444;
  --star:#f5c518;
  --purple-deep:#2a1530;
  --purple:#5b2a7a;
}
*{margin:0;padding:0;box-sizing:border-box}
html,body{width:1200px;height:3783px;overflow:hidden}
body{position:relative;background:var(--paper);font-family:"Montserrat",sans-serif;color:var(--ink)}
.abs{position:absolute}
.serif{font-family:"Playfair Display",serif}

/* header */
.site-header{left:0;top:0;width:1200px;height:100px;background:var(--paper)}
.brand{position:absolute;font-family:"Playfair Display",serif;font-weight:400;color:var(--ink);white-space:nowrap}
.site-header .brand{left:112px;top:30px;width:285px;text-align:center;font-size:32px}
.main-nav{position:absolute;left:548px;top:46px;display:flex;gap:0;width:540px;justify-content:space-between}
.main-nav a{font-family:"Playfair Display",serif;font-size:13px;color:#222;text-decoration:none;text-transform:uppercase}

/* hero */
.hero{left:0;top:100px;width:1200px;height:634px;background:linear-gradient(90deg,#1a0f1e,#3a1e44 30%,#2b1a24 70%,#1c1230)}
.hero-frame{position:absolute;left:157px;top:22px;width:886px;height:590px;border:8px solid var(--paper);background:linear-gradient(180deg,#2a1a12,#4a2e1c 55%,#1a1410)}
.hero .brand{left:0;right:0;top:440px;text-align:center;font-size:52px;color:var(--paper)}

/* ornament placeholder */
.ornament{position:absolute;height:14px;width:286px;background:linear-gradient(90deg,transparent,rgba(0,0,0,.28) 20%,rgba(0,0,0,.28) 80%,transparent);border-radius:7px}
.ornament.light{background:linear-gradient(90deg,transparent,rgba(255,255,255,.45) 20%,rgba(255,255,255,.45) 80%,transparent)}

/* sections */
.panel-dark{background:var(--dark)}
.panel-soft{background:var(--paper-soft)}
.section-title{position:absolute;font-family:"Playfair Display",serif;font-weight:700;text-transform:uppercase;white-space:nowrap}

.photo{position:absolute;border:1.5px solid var(--paper)}
.play-box{position:absolute;border:1.5px solid var(--paper);border-radius:0 44px 0 44px;display:flex;align-items:center;justify-content:center;color:var(--paper);font-size:13px;letter-spacing:3px;font-weight:500}

.btn{position:absolute;display:flex;align-items:center;justify-content:center;font-size:13px;font-weight:600;letter-spacing:4px;text-transform:uppercase;border-radius:6px 20px 6px 20px;text-decoration:none}
.btn-dark{background:var(--ink);color:var(--paper)}
.btn-light{background:var(--paper);color:var(--ink)}

.intro-copy{position:absolute;left:677px;top:948px;width:410px;font-size:13.2px;line-height:29.2px;color:#333}

.gallery-item{position:absolute;top:1562px;width:307px;height:273px;border-radius:0 44px 0 44px}

.review-name{position:absolute;left:112px;top:2256px;font-family:"Playfair Display",serif;font-size:30px;font-weight:400}
.review-quote{position:absolute;left:114px;top:2322px;width:420px;font-size:13.2px;line-height:29px;color:#333}
.stars{position:absolute;left:112px;top:2444px;display:flex;gap:8px}

.promo-lines{position:absolute;left:0;width:1200px;text-align:center;color:var(--paper);font-size:16px;font-weight:500}

.contact-band{left:0;top:3379px;width:1200px;height:257px;background:var(--band);color:var(--paper);text-align:center}
.contact-band p{position:absolute;left:0;width:1200px}

.site-footer{left:0;top:3636px;width:1200px;height:147px;background:var(--paper)}
</style>
</head>
<body>

<header class="abs site-header">
  <div class="brand">Marrow &amp; Tide</div>
  <nav class="main-nav">
    <a href="#">Home</a><a href="#">DJs</a><a href="#">Reviews</a><a href="#">Gallery</a><a href="#">Prices</a><a href="#">About</a><a href="#">Event Planner</a>
  </nav>
</header>

<section class="abs hero" role="img" aria-label="Blurred photo of a candlelit marquee dance floor seen from behind the DJ booth">
  <div class="hero-frame" role="img" aria-label="Photo of a DJ laptop set up in a fairy-lit wedding marquee"></div>
  <div class="brand">Marrow &amp; Tide</div>
</section>

<!-- intro -->
<div class="abs panel-dark" style="left:0;top:734px;width:600px;height:572px" role="img" aria-label="Dark floral pattern background"></div>
<div class="abs" style="left:600px;top:734px;width:600px;height:572px;background:var(--paper)"></div>
<div class="photo" style="left:112px;top:834px;width:412px;height:370px;border-radius:28px 0 0 0;background:linear-gradient(150deg,#1b3a3f,#0f5a4a 40%,#1a1412 75%)" role="img" aria-label="Photo of wedding guests dancing with arms raised under teal lights"></div>
<div class="play-box" style="left:448px;top:1084px;width:200px;height:179px;background:linear-gradient(160deg,#3a3228,#6a5a48)" role="img" aria-label="Video thumbnail of a bride on the dance floor">PLAY NOW</div>
<div class="ornament" style="left:696px;top:820px" role="img" aria-label="Decorative scroll ornament"></div>
<h1 class="section-title" style="left:677px;top:846px;font-size:42px">DJ Hire Surrey</h1>
<div class="ornament" style="left:696px;top:911px" role="img" aria-label="Decorative scroll ornament"></div>
<p class="intro-copy">Welcome to Marrow and Tide DJ hire Surrey. With 100% 5 star reviews on Bimmlo, having only started in September 2019, we are fast becoming the number 1 DJ hire company in Surrey. Whether you are looking to book for weddings, birthday parties or any occasion full of fizz and dancing, our London and Surrey wedding DJ provides a bespoke 5 star service, guaranteed to make you want to groove.</p>
<a class="btn btn-dark" href="#" style="left:677px;top:1169px;width:213px;height:52px">Learn More</a>

<!-- gallery -->
<div class="abs panel-soft" style="left:0;top:1306px;width:1200px;height:720px" role="img" aria-label="Subtle light chevron pattern background"></div>
<div class="ornament" style="left:457px;top:1419px" role="img" aria-label="Decorative scroll ornament"></div>
<h2 class="section-title" style="left:0;width:1200px;text-align:center;top:1442px;font-size:42px">Gallery</h2>
<div class="ornament" style="left:457px;top:1509px" role="img" aria-label="Decorative scroll ornament"></div>
<div class="gallery-item" style="left:112px;background:linear-gradient(160deg,#2a2a4a,#6a5a50 50%,#2a2020)" role="img" aria-label="Photo of a bride dancing among guests"></div>
<div class="gallery-item" style="left:447px;background:linear-gradient(180deg,#2a1c1a,#3a2a28 60%,#4a1f6a)" role="img" aria-label="Photo of a bar with purple uplighting"></div>
<div class="gallery-item" style="left:780px;background:linear-gradient(160deg,#5a2a9a,#3a2040 45%,#1e1620)" role="img" aria-label="Photo of guests dancing under purple marquee lights"></div>
<a class="btn btn-dark" href="#" style="left:494px;top:1877px;width:213px;height:52px">View More</a>

<!-- reviews -->
<div class="abs" style="left:0;top:2026px;width:600px;height:571px;background:var(--paper)"></div>
<div class="abs panel-dark" style="left:600px;top:2026px;width:600px;height:571px" role="img" aria-label="Dark floral pattern background"></div>
<div class="ornament" style="left:132px;top:2113px" role="img" aria-label="Decorative scroll ornament"></div>
<h2 class="section-title" style="left:0;width:550px;text-align:center;top:2134px;font-size:42px">Reviews</h2>
<div class="ornament" style="left:132px;top:2202px" role="img" aria-label="Decorative scroll ornament"></div>
<h3 class="review-name">Hannah Ellery</h3>
<p class="review-quote">"Have used many times for events, amazing guy! Always had guests comment to me about how fab the music was."<br>"Highly recommend, you won't be disappointed!"</p>
<div class="stars" aria-label="5 out of 5 stars">
  <svg width="26" height="25" viewBox="0 0 24 23"><path fill="#f5c518" d="M12 0l3.5 7.4 8.1 1-6 5.6 1.6 8L12 18l-7.2 4 1.6-8-6-5.6 8.1-1z"/></svg>
  <svg width="26" height="25" viewBox="0 0 24 23"><path fill="#f5c518" d="M12 0l3.5 7.4 8.1 1-6 5.6 1.6 8L12 18l-7.2 4 1.6-8-6-5.6 8.1-1z"/></svg>
  <svg width="26" height="25" viewBox="0 0 24 23"><path fill="#f5c518" d="M12 0l3.5 7.4 8.1 1-6 5.6 1.6 8L12 18l-7.2 4 1.6-8-6-5.6 8.1-1z"/></svg>
  <svg width="26" height="25" viewBox="0 0 24 23"><path fill="#f5c518" d="M12 0l3.5 7.4 8.1 1-6 5.6 1.6 8L12 18l-7.2 4 1.6-8-6-5.6 8.1-1z"/></svg>
  <svg width="26" height="25" viewBox="0 0 24 23"><path fill="#f5c518" d="M12 0l3.5 7.4 8.1 1-6 5.6 1.6 8L12 18l-7.2 4 1.6-8-6-5.6 8.1-1z"/></svg>
</div>
<a class="btn btn-dark" href="#" style="left:115px;top:2497px;width:211px;height:52px">Learn More</a>
<div class="photo" style="left:552px;top:2127px;width:410px;height:367px;background:linear-gradient(160deg,#5a2a8a,#8a5aa0 40%,#2a1a2a)" role="img" aria-label="Photo of two guests celebrating under purple lights"></div>
<div class="play-box" style="left:887px;top:2375px;width:200px;height:181px;background:linear-gradient(160deg,#1c1c1c,#0a0a0a)" role="img" aria-label="Video thumbnail of a dance floor">PLAY NOW</div>

<!-- promo -->
<div class="abs panel-dark" style="left:0;top:2597px;width:1200px;height:782px;background:#0c0c0c" role="img" aria-label="Dark floral pattern background"></div>
<div class="ornament light" style="left:457px;top:2708px" role="img" aria-label="Decorative scroll ornament"></div>
<h2 class="section-title" style="left:0;width:1200px;text-align:center;top:2733px;font-size:40px;color:var(--paper)">Surrey's Number 1 DJ Service</h2>
<div class="ornament light" style="left:457px;top:2799px" role="img" aria-label="Decorative scroll ornament"></div>
<p class="promo-lines" style="top:2872px">We are quite literally, UNBEATABLE.</p>
<p class="promo-lines" style="top:2935px">So if you are looking for the best DJ in London and Surrey, get in touch.</p>
<p class="promo-lines" style="top:2999px;line-height:31px">Wedding DJ London<br>Wedding DJ Surrey</p>
<p class="promo-lines" style="top:3094px">Party DJ London</p>
<p class="promo-lines" style="top:3158px">DJ Kingston</p>
<a class="btn btn-light" href="#" style="left:494px;top:3220px;width:213px;height:52px">Contact Us</a>

<!-- contact band -->
<section class="abs contact-band">
  <p style="top:85px;font-size:13px;letter-spacing:4.5px;font-weight:500">CHECK FOR AVAILABILITY,</p>
  <p style="top:110px;font-size:23px;letter-spacing:7px;font-weight:500">CALL NOW ON 0755 000 4821</p>
  <p style="top:143px;font-size:23px;letter-spacing:7px;font-weight:500">OR EMAIL: INFO@MARROWANDTIDE.COM</p>
</section>

<!-- footer -->
<footer class="abs site-footer">
  <p class="abs" style="left:112px;top:69px;font-size:12px;color:#111">Marrow and Tide © 2021. ALL RIGHTS RESERVED.</p>
  <div class="brand" style="left:457px;top:44px;width:286px;text-align:center;font-size:32px">Marrow &amp; Tide</div>
</footer>

</body>
</html>
```